holloway paving service

Needs to have phone number 0418259730 and email markholloway@brightmail.com.au.
ABN 62318470915
name mark holloway

For all your concreting solutions
Excavation
Exposed & colour concrete
House & shed slabs
Driveways
Landing & steps

Contact Information for Business Card

ph 0418259730
email markholloway@brightmail.com.au.
ABN 62318470915
name mark holloway

```html
<!DOCTYPE html>
<html lang="en">
<head>
<meta charset="utf-8">
<title>Holloway Paving Service – Business Card</title>
<link href="https://fonts.googleapis.com/css2?family=Montserrat:wght@400;600;700&display=swap" rel="stylesheet">
<style>
  :root {
    --backdrop: #e8e5e0;
    --card: #ffffff;
    --orange: #ea7a2a;
    --grey: #6b6b6b;
    --grey-dark: #5a5a5a;
  }
  * { margin: 0; padding: 0; box-sizing: border-box; }
  html, body {
    width: 1200px;
    height: 886px;
    overflow: hidden;
    background: var(--backdrop);
    font-family: "Montserrat", sans-serif;
  }
  .canvas {
    position: relative;
    width: 1200px;
    height: 886px;
    display: flex;
    justify-content: center;
    align-items: center;
    gap: 100px;
  }
  .card {
    width: 340px;
    height: 556px;
    background: var(--card);
    box-shadow: 0 2px 10px rgba(0,0,0,0.12);
    position: relative;
    display: flex;
    flex-direction: column;
    align-items: center;
    text-align: center;
  }

  /* Front */
  .card--front { padding-top: 120px; }
  .brand-mark {
    display: flex;
    flex-direction: column;
    align-items: center;
    gap: 18px;
  }
  .brand-mark__square {
    width: 110px;
    height: 110px;
    background: var(--orange);
  }
  .brand-mark__name {
    font-weight: 600;
    font-size: 15px;
    letter-spacing: 1px;
    color: var(--grey-dark);
    text-transform: uppercase;
  }
  .person-name {
    margin-top: 46px;
    font-weight: 700;
    font-size: 20px;
    letter-spacing: 1px;
    color: var(--orange);
    text-transform: uppercase;
  }
  .contact-list {
    list-style: none;
    margin-top: 16px;
    font-size: 13px;
    line-height: 1.55;
    color: var(--grey);
  }
  .contact-list__abn { margin-top: 12px; }

  /* Back */
  .card--back { padding-top: 64px; }
  .lockup {
    display: flex;
    align-items: center;
    gap: 14px;
  }
  .lockup__square {
    width: 36px;
    height: 36px;
    background: var(--orange);
  }
  .lockup__text { text-align: left; }
  .lockup__name {
    font-weight: 600;
    font-size: 13px;
    letter-spacing: 0.5px;
    color: var(--orange);
    text-transform: uppercase;
  }
  .lockup__phone {
    font-weight: 600;
    font-size: 11px;
    letter-spacing: 1px;
    color: var(--orange);
    margin-top: 3px;
  }
  .services {
    list-style: none;
    margin-top: auto;
    margin-bottom: 150px;
    font-size: 13px;
    line-height: 1.6;
    color: var(--grey);
  }
</style>
</head>
<body>
  <main class="canvas">
    <section class="card card--front" aria-label="Business card front">
      <div class="brand-mark">
        <span class="brand-mark__square" aria-hidden="true"></span>
        <span class="brand-mark__name">Holloway Paving Service</span>
      </div>
      <h1 class="person-name">Mark Holloway</h1>
      <ul class="contact-list">
        <li>0418259730</li>
        <li>markholloway@brightmail.com.au</li>
        <li>www.hollowaypaving.com.au</li>
        <li class="contact-list__abn">ABN 62318470915</li>
      </ul>
    </section>

    <section class="card card--back" aria-label="Business card back">
      <div class="lockup">
        <span class="lockup__square" aria-hidden="true"></span>
        <div class="lockup__text">
          <p class="lockup__name">Holloway Paving Service</p>
          <p class="lockup__phone">0418259730</p>
        </div>
      </div>
      <ul class="services">
        <li>Excavation</li>
        <li>Exposed &amp; colour concrete</li>
        <li>House &amp; shed slabs</li>
        <li>Driveways</li>
        <li>Landing &amp; steps</li>
      </ul>
    </section>
  </main>
</body>
</html>
```